Playful Website Design Needed Pet Sitting and Dog Walking Business

Need a simple one page Web Design Built on WordPress.
Sections:

About Us
Services Provided
Costs
Contact Us
Intake Form (Questionnaire that goes to email)
See us in Action

Industry/Entity Type

Pet Sitting and Dog Walking

Number of Pages Required

1 page

Font styles to use
Other font styles liked:
• See the Business Card Font and use that.

Colors
EE7325
F08F49
F5BC92
FAE3D3
FDF4ED

Requirements
Must have
• See attached Logo Design, with Font's and Colors Use these as theme guide

```html
<!DOCTYPE html>
<html lang="en">
<head>
<meta charset="utf-8">
<title>Paw Pals Sitting</title>
<link href="https://fonts.googleapis.com/css2?family=Montserrat:wght@400;500;600;700&family=Lato:wght@400;700&family=Dancing+Script:wght@700&display=swap" rel="stylesheet">
<style>
:root{
  --orange:#ee7325;
  --orange-2:#f08f49;
  --peach:#f5bc92;
  --cream:#fae3d3;
  --cream-2:#fdf4ed;
  --red:#e6512a;
  --yellow:#f7dc1e;
  --green:#6cb33a;
  --ink:#2b2b2b;
  --muted:#6b6b6b;
  --grey-bg:#f3f3f3;
  --white:#ffffff;
}
*{box-sizing:border-box;margin:0;padding:0}
html,body{width:1200px;height:4120px;overflow:hidden;background:var(--white)}
body{font-family:"Lato",sans-serif;color:var(--ink);position:relative}
.abs{position:absolute}
h1,h2,h3,h4{font-family:"Montserrat",sans-serif}
.btn{display:inline-block;font-family:"Montserrat",sans-serif;font-weight:700;font-size:13px;letter-spacing:.5px;padding:12px 26px;border-radius:30px;color:var(--white);background:var(--orange)}
.btn--yellow{background:var(--yellow);color:var(--ink)}
.accent{color:var(--orange)}
.rule{width:60px;height:4px;background:var(--yellow);border-radius:2px}

/* header */
.topbar{top:0;left:0;width:1200px;height:112px;background:var(--white);z-index:3}
.brand{left:110px;top:10px;display:flex;align-items:center;gap:10px;z-index:5}
.brand__dot{width:46px;height:46px;border-radius:50%;background:var(--orange)}
.brand__name{font-family:"Montserrat",sans-serif;font-weight:700;font-size:24px;color:var(--orange)}
.contact-strip{right:120px;top:10px;display:flex;gap:18px;align-items:center;font-size:12px;color:var(--muted)}
.contact-strip span{display:flex;align-items:center;gap:6px}
.social-dot{width:12px;height:12px;border-radius:50%;background:var(--orange);display:inline-block}
.nav{left:330px;top:58px;display:flex;gap:34px;font-family:"Montserrat",sans-serif;font-weight:600;font-size:13px}
.nav a{color:var(--ink);text-decoration:none}
.nav a.is-active{color:var(--orange);border-bottom:2px solid var(--orange);padding-bottom:6px}
.nav-cta{right:120px;top:48px}

/* hero */
.hero{top:112px;left:0;width:1200px;height:520px;background:linear-gradient(100deg,#d8581c 0%,#c9743a 30%,#8a8a55 55%,#5f7d3e 80%,#49652e 100%)}
.hero__welcome{left:130px;top:230px;font-family:"Dancing Script",cursive;font-size:44px;color:var(--white)}
.hero__title{left:130px;top:280px;font-size:80px;font-weight:600;line-height:84px;color:var(--white)}
.hero__text{left:130px;top:462px;width:420px;font-size:14px;line-height:20px;color:var(--white)}
.hero__cta{left:130px;top:518px}
.hero__dots{left:580px;top:598px;display:flex;gap:6px;z-index:2}
.hero__dots i{width:10px;height:10px;border-radius:50%;background:var(--white);opacity:.6}
.hero__dots i:first-child{opacity:1}

/* about */
.about__photo{left:100px;top:700px;width:470px;height:480px;border-radius:40% 40% 30% 30%;background:radial-gradient(circle at 50% 45%,#d9a15a,#b57a35 60%,var(--cream) 61%,var(--cream-2))}
.about__title{left:600px;top:770px;font-size:32px;font-weight:500}
.about__rule{left:600px;top:820px}
.about__text{left:600px;top:845px;width:490px;font-size:14px;line-height:22px;color:var(--muted)}
.about__cta{left:600px;top:1100px}

/* section heads */
.section-head{left:0;width:1200px;text-align:center}
.section-head h2{font-size:34px;font-weight:500}
.section-head .rule{margin:14px auto 24px}
.section-head p{width:760px;margin:0 auto;font-size:14px;line-height:22px;color:var(--muted)}

/* services */
.services{top:1220px;left:0;width:1200px;height:640px;background:var(--grey-bg)}
.service{width:330px;height:330px;border-radius:50%;display:flex;flex-direction:column;align-items:center;text-align:center;padding:50px 46px 0;color:var(--white)}
.service--feed{left:145px;top:1425px;background:var(--red)}
.service--walk{left:435px;top:1425px;background:var(--yellow);color:var(--ink);z-index:2;box-shadow:0 0 0 6px var(--white)}
.service--visit{left:725px;top:1425px;background:var(--green)}
.service__icon{width:52px;height:52px;border-radius:50%;background:var(--white);display:flex;align-items:center;justify-content:center;margin-bottom:14px}
.service h3{font-size:15px;font-weight:700;margin-bottom:10px}
.service p{font-size:12px;line-height:18px;margin-bottom:14px}
.service .btn{padding:8px 18px;font-size:11px;background:rgba(0,0,0,.18)}

/* costs */
.costs{top:1860px;left:0;width:1200px;height:580px;background:linear-gradient(135deg,var(--orange),#e0551c)}
.costs__title{left:100px;top:1950px;font-size:34px;font-weight:500;color:var(--white)}
.costs__rule{left:100px;top:1998px}
.costs__price{left:100px;top:2020px;font-size:24px;font-family:"Montserrat",sans-serif;font-weight:500;color:var(--white)}
.costs__text{left:100px;top:2070px;width:440px;font-size:14px;line-height:22px;color:var(--white)}
.costs__cta{left:100px;top:2250px}
.costs__photo{left:580px;top:1920px;width:500px;height:440px;border-radius:46% 54% 40% 60%/55% 45% 55% 45%;border:8px solid var(--cream);background:linear-gradient(160deg,#9fbf6a,#6e9440 55%,#a99a70)}

/* blog */
.blog-card{width:290px;top:2640px}
.blog-card--1{left:140px}.blog-card--2{left:455px;box-shadow:0 8px 24px rgba(0,0,0,.15);padding-bottom:18px}.blog-card--3{left:770px}
.blog-card__img{height:200px;border-radius:4px}
.blog-card h3{font-size:19px;font-weight:600;line-height:25px;margin:16px 10px 10px}
.blog-card p{font-size:13px;line-height:20px;color:var(--muted);margin:0 10px}

/* contact */
.contact{top:3090px;left:0;width:1200px;height:620px;background:var(--orange)}
.contact__photo{left:0;top:3120px;width:640px;height:560px;background:linear-gradient(135deg,#7fa64a,#54773a 55%,#a28a5a)}
.contact-form{left:660px;top:3140px;width:380px;height:520px;border-radius:20px;border:6px solid var(--yellow);background:linear-gradient(180deg,var(--orange-2),var(--orange));padding:40px 36px;box-shadow:0 10px 30px rgba(0,0,0,.2)}
.contact-form h2{color:var(--white);font-size:30px;font-weight:500;text-align:center}
.contact-form .rule{margin:12px auto 30px}
.field{height:44px;border-radius:22px;background:var(--white);margin-bottom:16px;padding:0 20px;display:flex;align-items:center;font-size:13px;color:#999}
.contact-form .btn{display:block;width:130px;margin:20px auto 0;text-align:center;background:var(--white);color:var(--orange)}

/* footer */
.footer-brand{left:120px;top:3790px;display:flex;align-items:center;gap:12px}
.footer-col{top:3780px}
.footer-col h4{font-size:16px;font-weight:700;color:var(--orange);margin-bottom:14px}
.footer-col li{list-style:none;font-size:13px;line-height:24px;color:var(--muted);display:flex;align-items:center;gap:8px}
.footer-col--quick{left:430px}.footer-col--other{left:630px}.footer-col--contact{left:830px}
.footer-social{left:830px;top:3990px;display:flex;gap:8px}
.footer-social i{width:26px;height:26px;border-radius:50%;background:var(--orange);display:block}
.copyright{left:0;top:4070px;width:1200px;height:50px;border-top:1px solid #eee;text-align:center;font-size:12px;line-height:50px;color:var(--muted)}
</style>
</head>
<body>

<!-- header -->
<div class="abs topbar"></div>
<div class="abs brand"><span class="brand__dot"></span><span class="brand__name">Paw Pals Sitting</span></div>
<div class="abs contact-strip" style="z-index:4">
  <span><svg width="12" height="12" viewBox="0 0 24 24"><path fill="#ee7325" d="M6.6 10.8a15 15 0 006.6 6.6l2.2-2.2a1 1 0 011-.25 11.4 11.4 0 003.6.6 1 1 0 011 1V20a1 1 0 01-1 1A17 17 0 013 4a1 1 0 011-1h3.5a1 1 0 011 1c0 1.25.2 2.45.6 3.6a1 1 0 01-.25 1z"/></svg>+1 555 010 2040</span>
  <span><svg width="12" height="12" viewBox="0 0 24 24"><path fill="#ee7325" d="M3 5h18v14H3z M3 5l9 7 9-7" stroke="#fff" stroke-width="1.5"/></svg>hello@pawpalssitting.com</span>
  <span>Login</span>
  <span><i class="social-dot"></i><i class="social-dot"></i><i class="social-dot"></i><i class="social-dot"></i></span>
</div>
<nav class="abs nav" style="z-index:4">
  <a class="is-active">HOME</a><a>ABOUT US</a><a>SERVICES PROVIDED</a><a>COSTS</a><a>CONTACT US</a>
</nav>
<span class="abs btn nav-cta" style="z-index:4">CONTACT FORM</span>

<!-- hero -->
<div class="abs hero" role="img" aria-label="Photo of a walker leading several dogs along a park path"></div>
<svg class="abs" style="left:0;top:560px;z-index:1" width="1200" height="100" viewBox="0 0 1200 100">
  <path d="M0 40 C300 110 600 0 900 40 S1150 60 1200 30 V100 H0z" fill="#f7dc1e"/>
  <path d="M0 55 C300 120 600 15 900 55 S1150 75 1200 45 V100 H0z" fill="#ee7325"/>
  <path d="M0 70 C300 130 600 30 900 70 S1150 90 1200 60 V100 H0z" fill="#fff"/>
</svg>
<div class="abs hero__welcome">Welcome To</div>
<h1 class="abs hero__title">Paw Pals<br>Sitting</h1>
<p class="abs hero__text">Lorem ipsum dolor sit amet, consectetur adipiscing elit, sed do eiusmod tempor incididunt ut labore et dolore magna aliqua.</p>
<span class="abs btn hero__cta">GET STARTED</span>
<div class="abs hero__dots"><i></i><i></i><i></i></div>

<!-- about -->
<div class="abs about__photo" role="img" aria-label="Photo of a golden retriever puppy sitting"></div>
<h2 class="abs about__title">About <span class="accent">Paw Pals Sitting</span></h2>
<div class="abs rule about__rule"></div>
<p class="abs about__text">Lorem ipsum dolor sit amet, consectetur adipiscing elit, sed do eiusmod tempor incididunt ut labore et dolore magna aliqua. Quis ipsum suspendisse ultrices gravida. Risus commodo viverra maecenas accumsan lacus vel facilisis. Sed ut perspiciatis unde omnis iste natus error sit voluptatem accusantium doloremque laudantium, totam rem aperiam, eaque ipsa quae ab illo inventore veritatis et quasi architecto beatae vitae dicta sunt explicabo. Nemo enim ipsam voluptatem quia voluptas sit aspernatur aut odit aut fugit, sed quia consequuntur magni dolores eos qui ratione voluptatem sequi nesciunt neque porro quisquam est.</p>
<span class="abs btn about__cta">LEARN MORE</span>

<!-- services -->
<div class="abs services"></div>
<div class="abs section-head" style="top:1290px">
  <h2>Our <span class="accent">Services Provided</span></h2>
  <div class="rule"></div>
  <p>Lorem ipsum dolor sit amet, consectetur adipiscing elit, sed do eiusmod tempor incididunt ut labore et dolore magna aliqua. Quis ipsum sus pendisse ultrices gravida. Risus commodo viverra maecenas accumsan lacus vel facilisis.</p>
</div>
<div class="abs service service--feed">
  <div class="service__icon"><svg width="28" height="28" viewBox="0 0 24 24"><path d="M3 12h18l-2 7H5z" fill="#e6512a"/></svg></div>
  <h3>WE FEED</h3>
  <p>Lorem ipsum dolor sit amet, consectetur adipiscing elit, sed do eiusmod tempor incididunt ut labore.</p>
  <span class="btn">LEARN MORE</span>
</div>
<div class="abs service service--walk">
  <div class="service__icon"><svg width="28" height="28" viewBox="0 0 24 24"><circle cx="8" cy="5" r="2.5" fill="#2b2b2b"/><path d="M8 8v7l-2 6M8 15l2 6M8 10l8 6" stroke="#2b2b2b" stroke-width="2" fill="none"/></svg></div>
  <h3>WALK AND PLAY WITH YOUR PET</h3>
  <p>Lorem ipsum dolor sit amet, consectetur adipiscing elit, sed do eiusmod tempor incididunt ut labore.</p>
  <span class="btn">LEARN MORE</span>
</div>
<div class="abs service service--visit">
  <div class="service__icon"><svg width="28" height="28" viewBox="0 0 24 24"><path d="M5 12l5 5 9-10" stroke="#6cb33a" stroke-width="3" fill="none"/></svg></div>
  <h3>EACH VISIT</h3>
  <p>Lorem ipsum dolor sit amet, consectetur adipiscing elit, sed do eiusmod tempor incididunt ut labore.</p>
  <span class="btn">LEARN MORE</span>
</div>

<!-- costs -->
<div class="abs costs"></div>
<svg class="abs" style="left:0;top:1850px" width="1200" height="40" viewBox="0 0 1200 40"><path d="M0 0 H1200 V10 C900 40 300 0 0 25z" fill="#f3f3f3"/></svg>
<h2 class="abs costs__title">Our Costs</h2>
<div class="abs rule costs__rule"></div>
<div class="abs costs__price">8$ Per Visit, 2 Visits a day</div>
<p class="abs costs__text">Lorem ipsum dolor sit amet, consectetur adipiscing elit, sed do eiusmod tempor incididunt ut labore et dolore magna aliqua. Quis ipsum suspendisse ultrices gravida. Risus commodo viverra maecenas accumsan lacus vel facilisis. Duis aute irure dolor in reprehenderit in voluptate velit esse cillum dolore eu fugiat nulla pariatur.</p>
<span class="abs btn btn--yellow costs__cta">LEARN MORE</span>
<div class="abs costs__photo" role="img" aria-label="Photo of a dog walker with a pack of small dogs on a sunny path"></div>
<svg class="abs" style="left:0;top:2400px" width="1200" height="50" viewBox="0 0 1200 50"><path d="M0 20 C300 50 800 0 1200 25 V50 H0z" fill="#fff"/></svg>

<!-- blog -->
<div class="abs section-head" style="top:2470px">
  <h2>Our <span class="accent">Latest Blog</span></h2>
  <div class="rule"></div>
  <p>Lorem ipsum dolor sit amet, consectetur adipiscing elit, sed do eiusmod tempor incididunt ut labore et dolore magna aliqua. Quis ipsum sus pendisse ultrices gravida. Risus commodo viverra maecenas accumsan lacus vel facilisis.</p>
</div>
<article class="abs blog-card blog-card--1">
  <div class="blog-card__img" role="img" aria-label="Photo of a person walking dogs in a town street" style="background:linear-gradient(135deg,#b9a58a,#7d8a6a)"></div>
  <h3>Lorem ipsum dolor sit amet consectetur adipiscing.</h3>
  <p>Lorem ipsum dolor sit amet, consectetur adipiscing elit, sed do eiusmod tempor incididunt ut labore et dolore magna.</p>
</article>
<article class="abs blog-card blog-card--2">
  <div class="blog-card__img" role="img" aria-label="Photo of a person playing with a dog on a grassy field" style="background:linear-gradient(180deg,#8fbbe0,#86a94e 55%,#5e7f33)"></div>
  <h3>Lorem ipsum dolor sit amet consectetur adipiscing.</h3>
  <p>Lorem ipsum dolor sit amet, consectetur adipiscing elit, sed do eiusmod tempor incididunt ut labore et dolore magna.</p>
</article>
<article class="abs blog-card blog-card--3">
  <div class="blog-card__img" role="img" aria-label="Photo of a dog walker with several dogs on leashes" style="background:linear-gradient(135deg,#9cab86,#5e6e4c)"></div>
  <h3>Lorem ipsum dolor sit amet consectetur adipiscing.</h3>
  <p>Lorem ipsum dolor sit amet, consectetur adipiscing elit, sed do eiusmod tempor incididunt ut labore et dolore magna.</p>
</article>

<!-- contact -->
<div class="abs contact"></div>
<div class="abs contact__photo" role="img" aria-label="Photo of two women sitting on grass with their dogs in a park"></div>
<svg class="abs" style="left:0;top:3080px" width="1200" height="60" viewBox="0 0 1200 60"><path d="M0 0 H1200 V20 C800 60 400 0 0 40z" fill="#fff"/></svg>
<svg class="abs" style="left:0;top:3650px" width="1200" height="70" viewBox="0 0 1200 70">
  <path d="M0 20 C400 70 800 0 1200 30 V70 H0z" fill="#f7dc1e"/>
  <path d="M0 35 C400 80 800 15 1200 45 V70 H0z" fill="#fff"/>
</svg>
<form class="abs contact-form">
  <h2>Contact Form</h2>
  <div class="rule"></div>
  <div class="field">First Name</div>
  <div class="field">Last Name</div>
  <div class="field">Email Address</div>
  <div class="field">Message</div>
  <span class="btn">SUBMIT</span>
</form>

<!-- footer -->
<div class="abs footer-brand"><span class="brand__dot" style="width:60px;height:60px"></span><span class="brand__name" style="font-size:26px">Paw Pals<br>Sitting</span></div>
<div class="abs footer-col footer-col--quick"><h4>QUICK LINKS</h4><ul><li>Home</li><li>About Us</li><li>Services Provided</li><li>Costs</li><li>Contact Us</li></ul></div>
<div class="abs footer-col footer-col--other"><h4>OTHER LINKS</h4><ul><li>FAQ's</li><li>About Us</li><li>Blog</li><li>Privacy Policy</li><li>Terms &amp; Conditions</li><li>Shipping Policy</li></ul></div>
<div class="abs footer-col footer-col--contact"><h4>CONTACT US</h4><ul>
  <li><svg width="12" height="14" viewBox="0 0 24 28"><path d="M12 0a9 9 0 00-9 9c0 7 9 19 9 19s9-12 9-19a9 9 0 00-9-9z" fill="#ee7325"/><circle cx="12" cy="9" r="3" fill="#fff"/></svg>123 Lorem ipsum dolor sit amet</li>
  <li><svg width="12" height="12" viewBox="0 0 24 24"><path fill="#ee7325" d="M6.6 10.8a15 15 0 006.6 6.6l2.2-2.2a1 1 0 011-.25 11.4 11.4 0 003.6.6 1 1 0 011 1V20a1 1 0 01-1 1A17 17 0 013 4a1 1 0 011-1h3.5a1 1 0 011 1c0 1.25.2 2.45.6 3.6a1 1 0 01-.25 1z"/></svg>+1 555 010 2040</li>
  <li><svg width="12" height="12" viewBox="0 0 24 24"><path fill="#ee7325" d="M6.6 10.8a15 15 0 006.6 6.6l2.2-2.2a1 1 0 011-.25 11.4 11.4 0 003.6.6 1 1 0 011 1V20a1 1 0 01-1 1A17 17 0 013 4a1 1 0 011-1h3.5a1 1 0 011 1c0 1.25.2 2.45.6 3.6a1 1 0 01-.25 1z"/></svg>+1 555 010 2041</li>
  <li><svg width="12" height="12" viewBox="0 0 24 24"><rect x="2" y="5" width="20" height="14" fill="#ee7325"/><path d="M2 5l10 8 10-8" stroke="#fff" stroke-width="1.5" fill="none"/></svg>hello@pawpalssitting.com</li>
</ul></div>
<div class="abs footer-social"><i></i><i></i><i></i><i></i></div>
<div class="abs copyright">© Copyrights 2022. Paw Pals Sitting | All rights reserved.</div>

</body>
</html>
```